we can communicate on this, but i want to follow the approach we took on Pellew|Marsh & Quinlan but i feel the card front needs the black background and the platinum and gold logo. The back? I am open. we can use the same info from PM&Q. Velmont Arc is an enhanced equity investment fund - basically a very exclusive boutique hedge fund that uses only stock options. very advanced things. hope you are interested

Contact Information for Business Card

Dr. Lewis T. Brennick, CFA
Scientifique de fusée financière
701.555.0143
LTBquant47@mailvantor.com

4718 Willow Creek Bend W.
West Fargo, ND 58078

No web site

Colors

Designer to choose colors to be used in the design.

Requirements
Nice to have
• I tend to prefer the most visible applications of the logo to include logo and name, the logo version with a black background and the gold and platinum components separated by the black. I see this working well for a single side (logo and name - this is card front to me).
• I am fairly open to other treatments on the reverse side with the data. To me, it makes sense to have a different color rendition of the logo on the reverse and it may be a muted black tone on tone or an oversized portion that would have spot UV. Or, the reverse may play with colors and layout
Should not have
• Other colors = no no
• Decorative font

```html
<!DOCTYPE html>
<html lang="en">
<head>
<meta charset="utf-8">
<title>Velmont Arc — Business Card</title>
<link href="https://fonts.googleapis.com/css2?family=Montserrat:wght@400;500;700&display=swap" rel="stylesheet">
<style>
  :root {
    --backdrop: #a3a3a3;
    --card-black: #2a2a2b;
    --card-white: #ffffff;
    --gold: #c29a2a;
    --platinum: #c9c7cc;
    --ink: #1b1b1b;
    --ink-soft: #2e2e2e;
  }
  * { margin: 0; padding: 0; box-sizing: border-box; }
  html, body {
    width: 1200px; height: 930px; overflow: hidden;
    background: var(--backdrop);
    font-family: "Montserrat", sans-serif;
  }
  .stage { position: relative; width: 1200px; height: 930px; }

  .card {
    position: absolute;
    width: 560px; height: 320px;
    border-radius: 22px;
    overflow: hidden;
  }

  /* Front */
  .card-front {
    left: 90px; top: 110px;
    background: var(--card-black);
    display: flex; align-items: center; justify-content: center; gap: 18px;
  }
  .front-mark {
    width: 54px; height: 54px; border-radius: 50%;
    background: var(--gold);
  }
  .front-name {
    font-weight: 700; font-size: 34px; letter-spacing: 3px;
    color: var(--platinum); text-transform: uppercase;
  }

  /* Back */
  .card-back {
    left: 550px; top: 500px;
    background: var(--card-white);
  }
  .back-rule { position: absolute; inset: 0; width: 100%; height: 100%; }
  .brand {
    position: absolute; left: 34px; top: 70px;
    display: flex; flex-direction: column; align-items: flex-start; gap: 10px;
  }
  .brand-mark {
    width: 74px; height: 74px; border-radius: 50%;
    background: var(--gold);
    margin-left: 6px;
  }
  .brand-name {
    font-weight: 700; font-size: 25px; letter-spacing: 1px;
    color: var(--ink); text-transform: uppercase;
  }
  .person {
    position: absolute; right: 44px; top: 40px; text-align: right;
  }
  .person-name {
    color: var(--gold); font-weight: 500; font-size: 20px;
    text-transform: uppercase; letter-spacing: .5px;
  }
  .person-title {
    color: var(--ink-soft); font-size: 13px; margin-top: 2px;
  }
  .accent-tab {
    position: absolute; right: 0; top: 40px;
    width: 10px; height: 30px; background: var(--gold);
  }
  .address {
    position: absolute; right: 44px; top: 200px; text-align: right;
    font-style: normal;
    color: var(--ink-soft); font-size: 14px; line-height: 1.4;
  }
  .contacts {
    position: absolute; left: 222px; bottom: 22px;
    list-style: none; color: var(--ink-soft); font-size: 15px; line-height: 1.6;
  }
  .contacts li { display: flex; align-items: center; gap: 8px; }
  .contacts svg { width: 11px; height: 11px; flex: none; }
</style>
</head>
<body>
<main class="stage">

  <section class="card card-front" aria-label="Card front">
    <span class="front-mark" aria-hidden="true"></span>
    <span class="front-name">Velmont Arc</span>
  </section>

  <section class="card card-back" aria-label="Card back">
    <svg class="back-rule" viewBox="0 0 560 320" aria-hidden="true">
      <line x1="535" y1="96" x2="205" y2="236" stroke="var(--gold)" stroke-width="1.5"/>
    </svg>

    <div class="brand">
      <span class="brand-mark" aria-hidden="true"></span>
      <span class="brand-name">Velmont Arc</span>
    </div>

    <span class="accent-tab" aria-hidden="true"></span>
    <div class="person">
      <p class="person-name">Dr. Lewis T. Brennick, CFA</p>
      <p class="person-title">Scientifique de fusée financière</p>
    </div>

    <address class="address">
      4718 Willow Creek Bend W.<br>
      West Fargo, ND 58078
    </address>

    <ul class="contacts">
      <li>
        <svg viewBox="0 0 12 12" aria-hidden="true"><path d="M2.5 1h2l1 3-1.3 1a6 6 0 0 0 2.8 2.8L8 6.5l3 1v2A1.5 1.5 0 0 1 9.5 11 8.5 8.5 0 0 1 1 2.5 1.5 1.5 0 0 1 2.5 1z" fill="var(--gold)"/></svg>
        701.555.0143
      </li>
      <li>
        <svg viewBox="0 0 12 12" aria-hidden="true"><rect x="1" y="2.5" width="10" height="7" fill="none" stroke="var(--gold)" stroke-width="1.2"/><path d="M1 2.5l5 4 5-4" fill="none" stroke="var(--gold)" stroke-width="1.2"/></svg>
        LTBquant47@mailvantor.com
      </li>
    </ul>
  </section>

</main>
</body>
</html>
```